New Template, new corporate image Kelvoran 2022

New template designs for google slides or PowerPoint. Match to new corporate image. The new website www.kelvoran-mx.example Needs to match our new version. Technology and Artificial Intelligence elements to reflect our type of work.
We are adding old version of template and will send elements for the new corporate images.
Please consider our website as the main corporate image.
Our templates are being used on customer presentations, webminars, internal work only.
We have our main name of company Kelvoran. Kelvoran has to be in all the templates.
Secondary logo or branded service is: Vastrelim.

Target Market(s)

Industrial users. Asset managers. Corporate visitors and customers.

Industry/Entity Type

Automotive. Chemical. Food and Beverage. Manufacturing

Other font styles liked:
• GE INSPIRA. RALEWAY

Colors
0054AA
0677BA
7BADD7
CADEEF
E8F1F8

Requirements
Must have
• Match to our elements on the new image. Use Brain Icons. Chips icons to connect equipments with software and control. Innovation.
Nice to have
• Unique images, machine images. Connecting machines and data elements. Template version for google slides. Image for industrial software for control equipment and saving money to manufacturers. Segments: Automotive, Chemical, Food and Beverages, Mining and pharmaceutical, Energy Management
Should not have
• old elements. not to much images of medical devices. Do not seems like a hospital.

```html
<!DOCTYPE html>
<html lang="es">
<head>
<meta charset="utf-8">
<title>Kelvoran – Plantilla corporativa 2022</title>
<link href="https://fonts.googleapis.com/css2?family=Mukta:wght@300;400;500&display=swap" rel="stylesheet">
<style>
  :root{
    --brand-blue:#0054AA;
    --brand-mid:#0677BA;
    --brand-sky:#7BADD7;
    --brand-pale:#CADEEF;
    --brand-mist:#E8F1F8;
    --ink-grey:#6d6d6d;
    --night:#1f1c30;
    --stage-top:#8c8c8c;
    --stage-bottom:#a8a8a8;
    --white:#ffffff;
  }
  *{margin:0;padding:0;box-sizing:border-box}
  html,body{width:1200px;height:1082px;overflow:hidden}
  body{font-family:"Mukta",sans-serif;background:linear-gradient(180deg,var(--stage-top),var(--stage-bottom) 60%);position:relative}
  .stage-wave{position:absolute;left:0;top:0;width:1200px;height:1082px}
  .slide{position:absolute;width:526px;height:295px;overflow:hidden;box-shadow:0 8px 22px rgba(0,0,0,.35)}
  .slide svg.shapes{position:absolute;inset:0;width:526px;height:295px}
  .wordmark{font-family:"Mukta",sans-serif;font-weight:400;letter-spacing:.5px;line-height:1;position:absolute}

  /* Slide: welcome */
  .slide--welcome{left:66px;top:78px;background:var(--brand-blue)}
  .welcome-kicker{position:absolute;left:23px;top:72px;color:var(--white);font-weight:300;font-size:28px;letter-spacing:.5px}
  .welcome-title{position:absolute;left:22px;top:116px;color:var(--white);font-weight:300;font-size:42px;letter-spacing:.5px;line-height:1}
  .welcome-body{position:absolute;left:23px;top:186px;width:220px;color:var(--white);font-weight:300;font-size:12.5px;line-height:22px}
  .slide--welcome .wordmark{left:290px;top:246px;font-size:28px;color:var(--brand-mid)}

  /* Slide: exhibitors */
  .slide--exhibitors{left:608px;top:78px;background:linear-gradient(120deg,#0a4ab8,#1c62c9 60%,#2a6fcf)}
  .slide--exhibitors .wordmark{left:15px;top:14px;font-size:15px;color:var(--white)}
  .exhibitors-title{position:absolute;left:14px;top:56px;color:var(--white);font-weight:300;font-size:38px;letter-spacing:.5px;line-height:1}
  .exhibitor{position:absolute;top:137px;width:160px;text-align:center}
  .exhibitor-num{width:64px;height:64px;margin:0 auto;border-radius:50%;background:var(--brand-pale);color:var(--brand-blue);font-weight:300;font-size:25px;line-height:66px}
  .exhibitor-text{margin-top:13px;color:var(--white);font-size:10.3px;line-height:15.6px;font-weight:400}

  /* Slide: about */
  .slide--about{left:66px;top:393px;background:var(--white)}
  .logo-tab{position:absolute;top:11px;right:8px;background:var(--brand-mist);padding:5px 8px 5px 6px}
  .logo-tab .wordmark{position:static;font-size:16px;color:var(--brand-mid)}
  .about-kicker{position:absolute;left:145px;top:32px;color:var(--ink-grey);font-weight:300;font-size:22px;line-height:1}
  .about-title{position:absolute;left:144px;top:74px;color:var(--brand-blue);font-weight:400;font-size:37px;line-height:1}
  .about-body{position:absolute;left:145px;top:123px;width:327px;color:var(--ink-grey);font-weight:300;font-size:11.6px;line-height:19.6px;text-align:justify}

  /* Slide: thanks */
  .slide--thanks{left:608px;top:393px;background:var(--white)}
  .thanks-photo{position:absolute;left:262px;top:58px;width:264px;height:237px;background:radial-gradient(ellipse at 40% 55%,#e9e9ea 0%,#dedfe1 45%,#f4f4f5 80%,rgba(255,255,255,0) 100%)}
  .thanks-title{position:absolute;left:34px;top:32px;color:var(--brand-blue);font-weight:400;font-size:54px;line-height:1;letter-spacing:.5px}
  .contact{position:absolute;left:33px;top:115px;list-style:none;color:var(--night)}
  .contact li{position:relative;padding-left:34px;font-size:16px;font-weight:300;line-height:24.5px;color:#2a2a3a}
  .contact svg{position:absolute;left:0;top:5px;width:15px;height:15px}

  /* Slide: cover */
  .slide--cover{left:66px;top:708px;background:linear-gradient(160deg,#1236c8,#0b3fc4 50%,#0a2aa6)}
  .cover-art{position:absolute;left:85px;top:8px;width:441px;height:287px;background:radial-gradient(ellipse at 55% 45%,#2d7cf2 0%,#1a55dd 35%,rgba(14,52,190,0) 75%)}
  .logo-pill{position:absolute;left:21px;top:25px;width:178px;height:45px;border-radius:23px;background:var(--white)}
  .logo-pill .wordmark{left:0;right:0;top:12px;text-align:center;font-size:22px;color:var(--brand-mid)}

  .hero-wordmark{position:absolute;left:700px;top:838px;font-size:100px;color:var(--brand-mid);font-family:"Mukta",sans-serif;font-weight:400;line-height:1;letter-spacing:1px}
</style>
</head>
<body>

<svg class="stage-wave" viewBox="0 0 1200 1082" aria-hidden="true">
  <path d="M0,790 Q600,690 1200,790 L1200,1082 L0,1082 Z" fill="var(--brand-blue)"/>
</svg>

<!-- Welcome slide -->
<section class="slide slide--welcome">
  <svg class="shapes" viewBox="0 0 526 295" aria-hidden="true">
    <polygon points="106,0 526,0 526,258" fill="var(--night)"/>
    <polygon points="314,127 526,258 526,295 222,295" fill="#f4f8fc"/>
  </svg>
  <div role="img" aria-label="Digital wireframe globe with connected network points" style="position:absolute;left:270px;top:-2px;width:236px;height:230px;border-radius:50%;background:radial-gradient(circle at 55% 40%,rgba(70,200,210,.55),rgba(40,120,150,.3) 45%,rgba(31,28,48,0) 72%);clip-path:polygon(0 0,100% 0,100% 100%,18% 58%)"></div>
  <p class="welcome-kicker">WELCOME TO</p>
  <h1 class="welcome-title">KELVORAN</h1>
  <p class="welcome-body">Lorem ipsum dolor sit amensectetur adipiscing elit, sed do eiusmod tempor incididunt ut lmagna aliqipsum</p>
  <span class="wordmark">kelvoran</span>
</section>

<!-- Exhibitors slide -->
<section class="slide slide--exhibitors">
  <div role="img" aria-label="Close-up photo of an electronic circuit board tinted blue" style="position:absolute;left:200px;top:0;width:326px;height:295px;background:linear-gradient(100deg,rgba(30,98,200,0),rgba(60,120,210,.45) 50%,rgba(40,100,200,.3))"></div>
  <svg class="shapes" viewBox="0 0 526 295" aria-hidden="true">
    <polygon points="436,0 526,0 526,38 477,70" fill="var(--brand-pale)"/>
    <polyline points="417,0 470,77 526,40" fill="none" stroke="var(--brand-pale)" stroke-width="1.5"/>
    <polygon points="0,262 45,295 0,295" fill="var(--brand-pale)"/>
  </svg>
  <span class="wordmark">kelvoran</span>
  <h2 class="exhibitors-title">EXPOSITORES</h2>
  <div class="exhibitor" style="left:10px">
    <div class="exhibitor-num">01</div>
    <p class="exhibitor-text">Lorem ipsum dolor sit nsectetur adipiscing elit, sed do eiusmod tempor incididunt ut labore et dolore magna aliqua.</p>
  </div>
  <div class="exhibitor" style="left:183px">
    <div class="exhibitor-num">02</div>
    <p class="exhibitor-text">Sed ut perspiciatis unde omnis iste natus error sit voluptatem accusantium doloremquet otam rem aperi</p>
  </div>
  <div class="exhibitor" style="left:356px">
    <div class="exhibitor-num">03</div>
    <p class="exhibitor-text">Lorem ipsum dolor sit nsectetur adipiscing elit, sed do eiusmod tempor incididunt ut labore et dolore magna aliqua.</p>
  </div>
</section>

<!-- About slide -->
<section class="slide slide--about">
  <svg class="shapes" viewBox="0 0 526 295" aria-hidden="true">
    <polygon points="0,0 112,0 0,50" fill="var(--brand-pale)"/>
    <polygon points="0,130 0,295 140,295" fill="var(--brand-pale)"/>
    <polygon points="0,120 0,134 167,295 150,295" fill="var(--white)"/>
    <polygon points="0,125 0,136 162,295 174,295" fill="var(--brand-blue)"/>
    <polygon points="0,114 0,125 174,295 186,295" fill="var(--white)"/>
  </svg>
  <div class="logo-tab"><span class="wordmark">kelvoran</span></div>
  <p class="about-kicker">ABOUT</p>
  <h2 class="about-title">KELVORAN</h2>
  <p class="about-body">Lorem ipsum dolor sit amensectetur adipiscing elited do eiusmod tempor incididunt dolore magna aliqipsumspendisseravidaisus commodo viverra maecenas accumsan lacus vel facilisiorem ipsum dolor sit amensectetur adipiscing elit, sed do eiusmod tempor incididunt dolore magna aliqipsumspendisseravidaisus commodo viverra maecenas accumsan lacus vel facilisis.</p>
</section>

<!-- Thanks slide -->
<section class="slide slide--thanks">
  <div class="thanks-photo" role="img" aria-label="Dotted world globe with two team members at a laptop"></div>
  <svg class="shapes" viewBox="0 0 526 295" aria-hidden="true">
    <polygon points="0,23 34,100 0,109" fill="var(--brand-pale)"/>
  </svg>
  <div class="logo-tab"><span class="wordmark">kelvoran</span></div>
  <h2 class="thanks-title">GRACIAS</h2>
  <ul class="contact">
    <li><svg viewBox="0 0 16 16" aria-hidden="true"><path d="M8 0.5C5 0.5 3 2.7 3 5.5 3 9.5 8 15.5 8 15.5S13 9.5 13 5.5C13 2.7 11 .5 8 .5Z" fill="var(--brand-blue)"/></svg>Calle Arbolada #218</li>
    <li>Colonia Verdal</li>
    <li>64100 Monterrey, NL.</li>
    <li>Conmutador 81 5550 1427</li>
    <li><svg viewBox="0 0 16 16" aria-hidden="true"><g fill="none" stroke="var(--brand-blue)" stroke-width="1.4"><circle cx="8" cy="8" r="6.8"/><ellipse cx="8" cy="8" rx="3" ry="6.8"/><path d="M1.2 8H14.8M2.3 4.5H13.7M2.3 11.5H13.7"/></g></svg>www.kelvoran-mx.example</li>
    <li><svg viewBox="0 0 16 16" aria-hidden="true"><rect x="0.5" y="3" width="15" height="10.5" rx="1" fill="var(--brand-blue)"/><path d="M1 4l7 5 7-5" fill="none" stroke="var(--white)" stroke-width="1.2"/></svg>informes@kelvoran-mx.example</li>
  </ul>
</section>

<!-- Cover slide -->
<section class="slide slide--cover">
  <div class="cover-art" role="img" aria-label="Isometric illustration of a glowing processor chip on a circuit board"></div>
  <div class="logo-pill"><span class="wordmark">kelvoran</span></div>
</section>

<span class="hero-wordmark">kelvoran</span>

</body>
</html>
```